Stonebrook Dugout case study mailout

Project must be designed in Adobe Illustrator.
I need a 8.5" x 11" brochure that will be folded in half and sent out as a mailout. I have attached our previous mailout and want some overlap in format to maintain our "brand". For the top part, I want the logo to stay on the left and blank space on the right (which is where my address label and stamp go).
I have attached the content in a word document (Stonebrook ).
I have attached a rough image of what I think the front could be, as far as the image. I would like the quote on the front as well, and the results.
I've included some photos of the dugout that are in the word document, whether or not they would show well on the brochure I don't know. These are the "after" photos and unfortunately I don't currently have the "before" ones.
Our website is www.ridgepumpworks.com and the system we sell is from www.velmora-tritex.com (also our company - manufacturing division).

```html
<!DOCTYPE html>
<html lang="en">
<head>
<meta charset="utf-8">
<title>Stonebrook Dugout Case Study Mailout</title>
<link href="https://fonts.googleapis.com/css2?family=Anton&family=Oswald:wght@600;700&family=Montserrat:wght@500;600;700&display=swap" rel="stylesheet">
<style>
:root{
  --blue:#1f6fc0;
  --blue-dark:#1459a3;
  --blue-light:#dbe9f7;
  --ink:#111;
  --white:#fff;
  --paper:#f2f3f5;
  --green:#3a9a3c;
  --stage:#b9b9b9;
}
*{box-sizing:border-box;margin:0;padding:0}
html,body{width:1200px;height:2486px;overflow:hidden}
body{background:var(--stage);font-family:"Montserrat",sans-serif;position:relative}
.spread{position:absolute;left:50px;top:817px;width:1100px;height:852px;display:flex;box-shadow:0 6px 18px rgba(0,0,0,.25)}
.page{position:relative;width:550px;height:852px;overflow:hidden}

/* back page */
.back{background:var(--paper)}
.back .panel{position:absolute;left:0;top:0;width:550px;height:610px;background:linear-gradient(180deg,#2a7ccc,#1c67b6)}
.brand{font-family:"Anton",sans-serif;font-size:40px;line-height:1;letter-spacing:.5px}
.back .brand{position:absolute;left:30px;top:30px;color:var(--white)}
.front .brand{position:absolute;left:52px;top:30px;color:var(--blue)}
.product{position:absolute;left:48px;top:158px;width:158px;height:450px;border-radius:6px;background:linear-gradient(180deg,#e8e9eb,#b6b9bd 60%,#5b5f63)}
.details{position:absolute;left:250px;top:30px;width:275px;color:var(--white)}
.details h3{font-family:"Oswald",sans-serif;font-weight:700;font-size:16px;letter-spacing:.2px;display:flex;align-items:center;gap:10px;margin-bottom:3px}
.details h3::after{content:"";flex:1;height:1px;background:rgba(255,255,255,.7)}
.details section{margin-bottom:20px}
.details p{font-size:12.3px;font-weight:600;line-height:1.36}
.details .plain{font-weight:500}
.details ul{list-style:none}
.details li{font-size:12.3px;font-weight:500;line-height:1.36;padding-left:15px;position:relative}
.details li::before{content:"";position:absolute;left:1px;top:4px;width:9px;height:9px;border-radius:50%;background:var(--white)}
.details li::after{content:"";position:absolute;left:3.5px;top:6px;width:4px;height:2px;border-left:1.5px solid var(--blue);border-bottom:1.5px solid var(--blue);transform:rotate(-45deg)}
.call{position:absolute;left:30px;top:630px;width:270px;text-align:center}
.call h2{font-family:"Oswald",sans-serif;font-weight:700;font-size:26px;color:var(--blue);letter-spacing:.3px}
.icons{display:flex;justify-content:center;gap:12px;margin:14px 0 12px}
.icons svg{width:22px;height:22px}
.call p{font-size:13.5px;font-weight:500;line-height:1.6;color:var(--ink)}
.supplier{position:absolute;left:330px;top:630px;width:190px;text-align:center;color:var(--blue);font-size:13px;font-weight:500}
.supplier .mark{display:flex;flex-direction:column;align-items:center;gap:6px;margin-top:14px}
.supplier .sq{width:70px;height:64px;border-radius:12px;background:var(--green)}
.supplier .name{font-family:"Montserrat",sans-serif;font-weight:700;font-size:20px;color:var(--green)}
.band{position:absolute;left:28px;bottom:0;width:494px;height:48px;background:var(--blue);border-radius:14px 14px 0 0;color:var(--white);display:flex;align-items:center;justify-content:center;gap:8px;font-weight:600}
.back .band{font-size:18px}
.front .band{font-size:13.5px}

/* front page */
.front{background:var(--paper)}
.front .sky{position:absolute;left:0;top:0;width:550px;height:330px;background:linear-gradient(180deg,#cfe2f3,#eef5fb 60%,#dfeaf4)}
.splash{position:absolute;left:0;top:135px;width:550px;height:70px;background:linear-gradient(180deg,rgba(31,111,192,0) 0%,#3f8ad3 45%,rgba(200,222,244,.4) 100%)}
.title{position:absolute;left:0;top:210px;width:550px;text-align:center}
.title h1{font-family:"Anton",sans-serif;font-weight:400;font-size:60px;line-height:1;color:var(--ink);letter-spacing:.5px}
.title h2{font-family:"Oswald",sans-serif;font-weight:700;font-size:28px;color:var(--blue);display:flex;align-items:center;justify-content:center;gap:12px;margin-top:4px}
.title h2::before,.title h2::after{content:"";width:66px;height:1.5px;background:var(--blue)}
.photo{position:absolute;left:0;top:322px;width:550px;height:288px;background:linear-gradient(180deg,#a9c3d6 0%,#6f8a5a 10%,#3d6f72 30%,#2c3a44 55%,#b5ab96 80%,#c9bfab 100%)}
.caption{position:absolute;left:0;top:572px;width:550px;text-align:center;font-family:"Oswald",sans-serif;font-weight:600;font-size:18px;color:var(--white);letter-spacing:.3px}
.results-tag{position:absolute;left:142px;top:598px;height:42px;display:flex;background:var(--blue);padding:3px}
.results-tag span{font-family:"Anton",sans-serif;font-size:30px;line-height:36px;padding:0 10px}
.results-tag .k{background:var(--white);color:var(--ink)}
.results-tag .v{color:var(--white)}
.results{position:absolute;left:14px;top:650px;width:522px;display:flex;justify-content:space-between}
.result{width:125px;text-align:center}
.result .badge{width:60px;height:60px;margin:0 auto 8px;background:var(--blue);border-radius:6px 26px 6px 26px;display:flex;align-items:center;justify-content:center}
.result h4{font-weight:600;font-size:14px;color:var(--blue);margin-bottom:3px}
.result p{font-size:10px;font-weight:500;line-height:1.3;color:var(--ink)}
</style>
</head>
<body>
<main class="spread">

  <article class="page back">
    <div class="panel"></div>
    <div class="brand">Ridge Pump<br>Works</div>
    <div class="product" role="img" aria-label="Photo of the ozone water treatment unit"></div>

    <div class="details">
      <section>
        <h3>COLONY INFORMATION</h3>
        <p>Name: Stonebrook Hutterite Colony<br>Water Usage: Dairy, Chickens, Swine, Field Crops, Drinking Water<br>Location: Central Alberta</p>
      </section>
      <section>
        <h3>WATER CONSUMPTION</h3>
        <p>Daily Use: Approximately 70,000 gallons<br>Dugout Volume: 30,000,000 gallons<br>Flow Rate: Continuous at 50 GPM</p>
      </section>
      <section>
        <h3>CISTERN OBSERVATIONS</h3>
        <p class="plain">Water clarity has significantly improved, allowing visibility to the bottom of the cistern, which was previously obscured by algae and other contaminants.</p>
      </section>
      <section>
        <h3>FILTRATION PERFORMANCE</h3>
        <ul>
          <li>Filter performance has greatly improved since introducing ozone to the dugouts.</li>
          <li>Small particulate and dissolved organic matter are being effectively flocculated, allowing filters to capture more material.</li>
          <li>By eliminating small particulate, less material escapes past the filters resulting in cleaner water.</li>
        </ul>
      </section>
      <section>
        <h3>ADDITIONAL BENEFITS</h3>
        <ul>
          <li>The brown ring that used to form in residential drains and tubs is no longer occurring.</li>
        </ul>
      </section>
    </div>

    <div class="call">
      <h2>CALL US ANYTIME!</h2>
      <div class="icons">
        <svg viewBox="0 0 22 22" aria-label="Phone"><circle cx="11" cy="11" r="11" fill="#1f6fc0"/><path d="M7.5 6.5l2 0 1 2.5-1.2 1a6 6 0 0 0 2.7 2.7l1-1.2 2.5 1v2c-4.5.3-8.3-3.5-8-8z" fill="#fff"/></svg>
        <svg viewBox="0 0 22 22" aria-label="Email"><circle cx="11" cy="11" r="11" fill="#1f6fc0"/><rect x="6" y="7.5" width="10" height="7" rx="1" fill="#fff"/><path d="M6.5 8l4.5 3.5L15.5 8" stroke="#1f6fc0" stroke-width="1.2" fill="none"/></svg>
        <svg viewBox="0 0 22 22" aria-label="Website"><circle cx="11" cy="11" r="11" fill="#1f6fc0"/><circle cx="11" cy="11" r="5" fill="none" stroke="#fff" stroke-width="1.3"/><ellipse cx="11" cy="11" rx="2.2" ry="5" fill="none" stroke="#fff" stroke-width="1.1"/><path d="M6 11h10" stroke="#fff" stroke-width="1.1"/></svg>
      </div>
      <p>555-014-2290 | 1-800-555-0147<br>info@ridgepumpworks.com<br>www.ridgepumpworks.com</p>
    </div>

    <div class="supplier">
      Proud supplier of
      <div class="mark"><div class="sq"></div><div class="name">Velmora Tritex</div></div>
    </div>

    <div class="band">
      <svg width="14" height="14" viewBox="0 0 14 14"><circle cx="7" cy="7" r="6" fill="none" stroke="#fff" stroke-width="1.4"/><ellipse cx="7" cy="7" rx="2.6" ry="6" fill="none" stroke="#fff" stroke-width="1.2"/><path d="M1 7h12" stroke="#fff" stroke-width="1.2"/></svg>
      www.velmora-tritex.com
    </div>
  </article>

  <article class="page front">
    <div class="sky"></div>
    <div class="splash" role="img" aria-label="Splash of blue water with bubbles"></div>
    <div class="brand">Ridge Pump<br>Works</div>
    <div class="title">
      <h1>ADVANCED OZONE</h1>
      <h2>Water Treatment Solutions</h2>
    </div>
    <div class="photo" role="img" aria-label="Photo of the lined farm dugout with clear water and a pump on the sandy bank"></div>
    <div class="caption">OZONE CASE STUDY - STONEBROOK HUTTERITE COLONY</div>
    <div class="results-tag"><span class="k">DUGOUT</span><span class="v">RESULTS</span></div>

    <div class="results">
      <div class="result"><div class="badge" role="img" aria-label="ORP icon"></div><h4>Improved ORP</h4><p>Within 2 weeks,<br>the ORP increase<br>by approximately<br>350mV</p></div>
      <div class="result"><div class="badge" role="img" aria-label="Algae icon"></div><h4>Reduced Algae</h4><p>1" think layer<br>of algae was<br>replace by a thin<br>layer of sand</p></div>
      <div class="result"><div class="badge" role="img" aria-label="Foam icon"></div><h4>Foam Reduction</h4><p>Abundant foam<br>collecting at<br>the edge almost<br>eliminated</p></div>
      <div class="result"><div class="badge" role="img" aria-label="Water clarity icon"></div><h4>Water Clarity</h4><p>Greenish, opaque<br>water became<br>shimmering blue<br>&amp;transparent</p></div>
    </div>

    <div class="band">“ We’ve never seen water this clear before! ” - Dale, plumber</div>
  </article>

</main>
</body>
</html>
```